business card deign

Logo needs the following on it.
1. attached logo
2. Tagline - "If it keeps a snack fresh or the crowd cheering...we make it!"
3. Name- Dalton Pikes, Founder and CPO
4. Address - 412 E. Carver Avenue, Ste 2207, Harlow, GA. 33917
5. Phone - 555.318.4726

```html
<!DOCTYPE html>
<html lang="en">
<head>
<meta charset="utf-8">
<title>Bounda Business Card</title>
<link href="https://fonts.googleapis.com/css2?family=Montserrat:wght@400;700&display=swap" rel="stylesheet">
<style>
  :root {
    --backdrop: #3b3b3b;
    --card: #ffffff;
    --ink: #111111;
    --ink-soft: #3a3a3a;
    --band: #0c0c0c;
    --band-text: #ffffff;
  }
  * { box-sizing: border-box; margin: 0; padding: 0; }
  html, body { width: 1200px; height: 689px; overflow: hidden; }
  body {
    background: var(--backdrop);
    font-family: "Montserrat", sans-serif;
    display: flex;
    align-items: center;
    justify-content: center;
    gap: 40px;
  }
  .card {
    position: relative;
    width: 540px;
    height: 309px;
    background: var(--card);
    border-radius: 22px;
    overflow: hidden;
    box-shadow: 0 14px 30px rgba(0,0,0,0.45);
  }
  .brand {
    display: flex;
    align-items: center;
    gap: 12px;
    color: var(--ink);
    font-weight: 700;
    letter-spacing: 0.28em;
    white-space: nowrap;
  }
  .brand-dot {
    width: 14px; height: 14px;
    border-radius: 50%;
    background: var(--ink);
  }
  .card-front .brand {
    position: absolute;
    left: 50%; top: 50%;
    transform: translate(-50%, -50%);
    font-size: 46px;
  }
  .card-back .brand {
    position: absolute;
    left: 50%; top: 52px;
    transform: translateX(-50%);
    font-size: 30px;
  }
  .card-back .brand-dot { width: 10px; height: 10px; }
  .details {
    position: absolute;
    left: 0; right: 0; top: 136px;
    display: flex;
    justify-content: center;
    align-items: stretch;
  }
  .person {
    text-align: right;
    padding-right: 20px;
    display: flex;
    flex-direction: column;
    justify-content: flex-end;
  }
  .person-name { font-size: 19px; font-weight: 700; color: var(--ink); }
  .person-title { font-size: 14px; font-weight: 400; color: var(--ink-soft); margin-top: 2px; }
  .divider { width: 1px; height: 92px; background: var(--ink); }
  .contact {
    padding-left: 20px;
    font-size: 13px;
    color: var(--ink-soft);
    line-height: 1.45;
  }
  .contact-phone { display: flex; align-items: center; gap: 6px; margin-bottom: 10px; }
  .contact-phone svg { width: 12px; height: 12px; fill: var(--ink); }
  .tagline-band {
    position: absolute;
    left: 0; right: 0; bottom: 22px;
    height: 30px;
    background: var(--band);
    display: flex;
    align-items: center;
    justify-content: center;
    gap: 14px;
    color: var(--band-text);
    font-size: 13px;
    letter-spacing: 0.02em;
    white-space: nowrap;
  }
  .band-dot {
    width: 8px; height: 8px;
    border-radius: 50%;
    background: var(--band-text);
  }
</style>
</head>
<body>
  <section class="card card-front">
    <div class="brand"><span class="brand-dot"></span>BOUNDA</div>
  </section>

  <section class="card card-back">
    <div class="brand"><span class="brand-dot"></span>BOUNDA</div>
    <div class="details">
      <div class="person">
        <p class="person-name">Dalton Pikes</p>
        <p class="person-title">Founder and CPO</p>
      </div>
      <div class="divider"></div>
      <div class="contact">
        <p class="contact-phone">
          <svg viewBox="0 0 24 24" aria-hidden="true"><path d="M6.6 10.8a15.1 15.1 0 0 0 6.6 6.6l2.2-2.2a1 1 0 0 1 1-.25 11.4 11.4 0 0 0 3.6.57 1 1 0 0 1 1 1V20a1 1 0 0 1-1 1A17 17 0 0 1 3 4a1 1 0 0 1 1-1h3.5a1 1 0 0 1 1 1c0 1.25.2 2.45.57 3.57a1 1 0 0 1-.25 1z"/></svg>
          555.318.4726
        </p>
        <p>412 E. Carver Avenue, Ste</p>
        <p>2207, Harlow, GA. 33917</p>
      </div>
    </div>
    <div class="tagline-band">
      <span>If it keeps a snack fresh or the crowd cheering...we make it!</span>
      <span class="band-dot"></span>
    </div>
  </section>
</body>
</html>
```